A unique communication angle to crowdfunding

Looking for a fresh redesign of a crowd funding website that deals in real estate. I already have the content, but am looking to take the design to the next level.

Existing real estate crowd funding sites focus on the real estate. I want to explore communication angle that:
- puts the investor in the centre of the communication: "become a baron"
- highlights the international nature (international properties, international investors)

There's also quite a lot of copy on the site, as we need to explain the service in quite a bit of detail. There's room to reduce the copy and replace with graphics. Could also consider clicking to see different text (see our difference section in http://galleonfairs.com)

The backend of the platform is already being worked on by a specialist crowd funding service provider.

In total there are 5 pages to be designed.

The homepage is really important. Right now it looks quite dated. It doesn't have a great layout. Note there is no mobile version of the website, so the pages need to be seen well on mobile devices. When looking at the brief, refer to the following links too:

current website:
http://pennyduke.com

some revisions made so far:
http://preview.stakeharbor.com/7K3LQ9

Attached are logo files and another file which contained copy for the pages. No need to rework the logo.

Please make sure to use the same copy in the brief on the webpages, to ensure the layouts work. Designers are free to propose images they feel work on the pages.

I would like to see if rather than tweaking the pages, it's possible to come up with a better design concept. If the 5 pages are accepted, there's a chance I'll request an additional 4 pages.
Updates

Please note the font used in the logo is called "harabara" in case you decide to use it in any of the titles, etc.

Please note there is one additional page for which we would like to review designs. Note the page would be a template to be used on all future real estate detail pages. Here is an example of the current design for reference:

http://pennyduke.com/projects/view/14

In total there are 5 page designs required, (homepage + 4)

Thank you

FYI -

Just a quick note to give information from similar UK real estate crowdfunding sites:
http://www.housewalrus.co.uk
http://tiderock.co.uk
https://www.fundquarry.com

Of the above, only tiderock has a nice clean looking landing page. Information is clear and well laid out.

Hi all, just uploaded a new file in the brief. Contains some comments and a website reference. I thought it may help to explain how we could convey international aspect as well as how we could convey images in a more modern way. This is an option you can consider, but its entirely up to you how how answer the brief. Thanks!

Reason: As requested by some designers needing more time to complete their work. Continue to share your work in progress and receive timely feedback before the deadline.

We would like to let you know that we have just shortlisted the best designs. Together with that, we have also passed some detailed feedback to all designers who weren't shortlisted. If we didn't contact you, please let us know. If you haven't submitted a design or are working on revisions, please note these will no longer be taken into account now. We hope you understand that we need to close the project today. Thank you all once again for your great work and design concepts. Here's hoping we meet again on a future design brief. Cheers, pennyduke team.

Target Market(s)

At the moment, only rich are able to buy real estate. With this service, anyone can become a landlord. Target buyers:

Young professionals, looking to diversify from stock market and lower risk
People nearing retirement, looking for stable rental incomes
Retirees - looking to supplement pensions with possibility of capital gains
Parents - looking for a way to save long term for their children (instead of low interest paying bank accounts)

Industry/Entity Type

Communication

Font styles to use
Sans Serif
Other font styles liked:
• harabara

Colors
add136
f5f9eb
959595
000000

Requirements
Must have
• Overall, the site must convey "whoever you are, you too can become a landlord", and that you don't need to be wealthy to invest in real estate. See

Communication should put the investor (or the baron) at the centre. The investor can be any of those described in the target market.

Show the aspirational side of property ownership.

In addition to the investor/baron character, the second main theme is international. No other real estate crowdfunding website highlights this.
Nice to have
• Banner could show different consumer types, to illustrate that the service can appeal to many different profiles. Refer to attached file "home page reference - plainasbread.com" as an example of how this could be done.

Aim to show the international side of the service. Properties around the world, investors around the world.

```html
<!DOCTYPE html>
<html lang="en">
<head>
<meta charset="utf-8">
<title>pennyduke – Social real estate investment</title>
<link rel="stylesheet" href="https://fonts.googleapis.com/css2?family=Open+Sans:wght@400;600;700&family=Varela+Round&display=swap">
<style>
:root{
  --green:#8dc63f;
  --green-dark:#74a92c;
  --green-pale:#f5f9eb;
  --grey:#959595;
  --grey-light:#f2f2f2;
  --grey-line:#dcdcdc;
  --text:#555;
  --dark:#3a3a3a;
  --black:#000;
  --white:#fff;
}
*{box-sizing:border-box;margin:0;padding:0}
html,body{width:1200px;height:3000px;overflow:hidden}
body{font-family:"Open Sans",Arial,sans-serif;color:var(--text);background:var(--white);font-size:14px;position:relative}
.heading{font-family:"Varela Round","Open Sans",sans-serif;color:var(--green);font-weight:400}

/* header */
.site-header{height:96px;position:relative;background:var(--white)}
.brand{position:absolute;left:154px;top:24px;display:flex;align-items:center;gap:10px}
.brand-dot{width:40px;height:40px;border-radius:50%;background:var(--green)}
.brand-name{font-size:26px;font-weight:700;color:var(--green)}
.follow{position:absolute;left:618px;top:22px;display:flex;align-items:center;gap:8px;font-size:13px;color:var(--dark)}
.social-box{width:36px;height:28px;background:var(--green)}
.social-box.alt{background:var(--white);border:1px solid var(--grey-line)}
.search{position:absolute;left:810px;top:22px;display:flex}
.search-field{width:206px;height:28px;background:var(--grey-light);font-size:11px;color:#aaa;padding:7px 10px}
.search-btn{width:38px;height:28px;background:#555;display:flex;align-items:center;justify-content:center}
.main-nav{position:absolute;right:144px;top:66px;display:flex;gap:28px;font-size:11px;font-weight:600;text-transform:uppercase;color:#666}
.main-nav .active{color:var(--dark);border-bottom:2px solid var(--green);padding-bottom:6px}

/* hero */
.hero{height:388px;position:relative;overflow:hidden}
.hero-photo{position:absolute;inset:0;background:linear-gradient(100deg,#eef0ea 0%,#cfd5c6 30%,#6f8a5a 50%,#2f8f45 62%,#a99063 78%,#6d5a3c 100%)}
.hero-caption{position:absolute;left:144px;top:104px;width:506px;height:80px;background:rgba(141,198,63,.92);padding:10px 18px;color:var(--white)}
.hero-caption h1{font-size:24px;font-weight:600;color:#1e2a12;line-height:1.3}
.hero-caption p{font-size:13px}
.hero-arrow{position:absolute;top:172px;width:44px;height:44px;border-radius:50%;background:rgba(30,30,30,.75);border:2px solid rgba(255,255,255,.5)}
.hero-arrow.prev{left:94px}.hero-arrow.next{left:1062px}
.hero-dots{position:absolute;left:130px;top:462px;top:366px;display:flex;gap:6px}
.hero-dots span{width:9px;height:9px;border-radius:50%;background:#666}
.hero-dots span:first-child{background:var(--green)}

/* intro */
.intro{height:306px;text-align:center;padding-top:46px}
.intro h2{font-size:30px}
.rule{width:410px;height:1px;background:var(--grey-line);margin:14px auto 22px}
.intro p{font-size:13.5px;line-height:1.7;margin:0 auto 24px;width:790px}
.hl{color:var(--green);font-weight:600}

/* paths */
.paths{height:302px;background:var(--grey-light);display:flex;justify-content:center;gap:60px;padding-top:48px}
.path{width:368px}
.path-card{height:146px;background:var(--white);border:1px solid var(--grey-line);display:flex;gap:18px;padding:26px 16px}
.path-icon{width:78px;height:78px;border-radius:50%;background:#3f3f3f;flex:none;display:flex;align-items:center;justify-content:center}
.path-card h3{font-size:21px;margin-bottom:6px}
.path-card p{font-size:13px;line-height:1.7}
.path-btn{margin-top:12px;height:46px;background:var(--green);border-bottom:4px solid var(--green-dark);color:var(--white);font-size:19px;font-weight:700;text-align:center;line-height:42px}

/* projects */
.projects{height:622px;text-align:center;padding-top:30px}
.projects h2{font-size:22px}
.projects .lead{font-size:13px;line-height:1.8;margin:10px auto 0;width:560px}
.project-row{display:flex;justify-content:center;gap:20px;margin-top:36px;text-align:left}
.project{width:292px;height:416px;border:1px solid var(--grey-line);background:var(--white)}
.project.featured{box-shadow:0 2px 6px rgba(0,0,0,.25)}
.project-photo{height:206px;position:relative}
.photo-a{background:linear-gradient(180deg,#5c95d6 0%,#8ab8e6 45%,#9c5a3f 60%,#7b8a62 100%)}
.photo-b{background:linear-gradient(180deg,#7ab0e6 0%,#c7dcf1 40%,#a56e51 60%,#8e9b76 100%)}
.photo-c{background:linear-gradient(180deg,#5aa0e6 0%,#b9d7f2 40%,#e6dfd0 62%,#5d7f3b 100%)}
.price-tag{position:absolute;left:0;top:0;background:var(--green);color:var(--white);font-size:10px;font-weight:700;padding:5px 8px}
.launch-tag{position:absolute;left:0;top:24px;background:#555;color:#e8e8e8;font-size:9px;padding:4px 8px}
.project-body{padding:12px 12px}
.project h3{font-size:14px;color:var(--green);font-weight:600;margin-bottom:8px}
.project p{font-size:11.5px;line-height:1.7;height:60px}
.project-funding{border-top:1px solid var(--grey-line);margin-top:12px;padding:8px 12px 0}
.funded{font-size:12px;font-weight:700;color:#444}
.bar{height:20px;border:1px solid var(--grey-line);background:var(--white);margin-top:4px;position:relative;font-size:11px;text-align:center;line-height:18px;color:#333}
.bar-fill{position:absolute;left:0;top:0;bottom:0;background:var(--green)}
.bar span{position:relative}
.details{text-align:center;font-size:12.5px;margin-top:8px;color:#666}
.featured .details{color:var(--green);font-weight:600}

/* community */
.community{height:422px;position:relative;text-align:center;color:#d8d8d8;background:linear-gradient(180deg,#555 0%,#3a3a3a 40%,#202020 100%)}
.community-backdrop{position:absolute;inset:0;background:radial-gradient(ellipse at 50% 35%,rgba(255,255,255,.12),transparent 60%)}
.community h2{position:relative;padding-top:54px;font-size:21px}
.community .lead{position:relative;font-size:13.5px;line-height:1.75;margin:10px auto 0;width:620px;color:#999}
.stats{position:relative;display:flex;justify-content:center;gap:40px;margin-top:42px}
.stat{width:268px;height:150px;position:relative}
.stat-map{position:absolute;inset:0 20px 48px;background:rgba(150,150,150,.22);border-radius:40px}
.stat-figure{position:relative;padding-top:34px;font-size:19px;font-weight:700;color:var(--green);line-height:1.3;height:100px}
.stat-label{position:relative;font-size:13.5px;line-height:1.7;color:#ccc}

/* press */
.press{height:264px;position:relative}
.press-box{position:absolute;left:144px;top:60px;width:912px;height:192px;border:1px solid var(--grey-line)}
.press-tag{position:absolute;left:522px;top:42px;width:174px;height:38px;background:var(--green);color:#1e2a12;font-size:15px;font-weight:600;text-align:center;line-height:38px}
.press-row{position:absolute;left:0;right:0;display:flex;justify-content:center;gap:36px;align-items:center}
.press-row.first{top:76px}.press-row.second{top:138px}
.badge{height:26px;background:#cfcfcf;border-radius:3px}

/* footer */
.skyline{height:140px;background:linear-gradient(180deg,#fff 0%,#e6e6e6 35%,#9a9a9a 100%)}
.footer-bar{height:64px;background:#3b3b3b;display:flex;align-items:center;padding:0 144px;color:var(--green);font-size:15px}
.footer-bar .social-box{width:38px;height:30px;background:transparent;border:1px solid var(--green);margin-left:10px}
.footer-bar .copy{margin-left:auto;font-size:12px}
.legal{padding:22px 144px 0;font-size:12.5px;line-height:1.85;color:#666;position:relative}
.legal p{margin-bottom:22px}
.legal .intro-note{width:590px}
.group-name{position:absolute;right:198px;top:26px;font-size:36px;color:#333;font-weight:400}
</style>
</head>
<body>

<header class="site-header">
  <div class="brand"><span class="brand-dot"></span><span class="brand-name">pennyduke</span></div>
  <div class="follow">Follow us on <span class="social-box"></span><span class="social-box alt"></span></div>
  <div class="search">
    <div class="search-field">Search...</div>
    <div class="search-btn"><svg width="14" height="14" viewBox="0 0 14 14"><circle cx="6" cy="6" r="4.2" fill="none" stroke="#fff" stroke-width="1.8"/><line x1="9" y1="9" x2="13" y2="13" stroke="#fff" stroke-width="2"/></svg></div>
  </div>
  <nav class="main-nav">
    <span class="active">Home</span><span>Sign in</span><span>How it works</span><span>Discover a project</span><span>The baron blog</span><span>Find out more</span>
  </nav>
</header>

<section class="hero">
  <div class="hero-photo" role="img" aria-label="Green model houses standing on stacks of coins"></div>
  <div class="hero-caption">
    <h1>One property at a time</h1>
    <p>Invest from 1% in a property. Diversify across cities and properties.</p>
  </div>
  <div class="hero-arrow prev"><svg width="40" height="40" viewBox="0 0 40 40"><path d="M23 13 L16 20 L23 27" fill="none" stroke="#fff" stroke-width="2"/></svg></div>
  <div class="hero-arrow next"><svg width="40" height="40" viewBox="0 0 40 40"><path d="M17 13 L24 20 L17 27" fill="none" stroke="#fff" stroke-width="2"/></svg></div>
  <div class="hero-dots"><span></span><span></span><span></span><span></span></div>
</section>

<section class="intro">
  <h2 class="heading">Social real estate investment</h2>
  <div class="rule"></div>
  <p>By harnessing the power of crowds, it's possible to become a landlord in locations around the world. Forget the burden of financing <span class="hl">100%</span> of the purchase.</p>
  <p>Leave the day to day management of your property portfolio to us.</p>
  <p>Start with <span class="hl">1%</span> in a project and plan your steps to becoming a true baron</p>
</section>

<section class="paths">
  <div class="path">
    <div class="path-card">
      <div class="path-icon"><svg width="46" height="46" viewBox="0 0 46 46" fill="none" stroke="#8dc63f" stroke-width="2"><rect x="6" y="18" width="12" height="24"/><rect x="20" y="8" width="12" height="34"/><rect x="34" y="24" width="8" height="18"/></svg></div>
      <div><h3 class="heading">Find properties</h3><p>Sign up to browse the portfolio. Your journey to becoming a real estate baron starts here.</p></div>
    </div>
    <div class="path-btn">Become a member</div>
  </div>
  <div class="path">
    <div class="path-card">
      <div class="path-icon"><svg width="46" height="46" viewBox="0 0 46 46" fill="#8dc63f"><circle cx="12" cy="12" r="5"/><circle cx="23" cy="9" r="5"/><circle cx="34" cy="12" r="5"/><rect x="7" y="19" width="10" height="20" rx="3"/><rect x="18" y="16" width="10" height="24" rx="3"/><rect x="29" y="19" width="10" height="20" rx="3"/></svg></div>
      <div><h3 class="heading">Find Buyers</h3><p>Submit a property or development and raise funds from our real estate barons.</p></div>
    </div>
    <div class="path-btn">Submit a property</div>
  </div>
</section>

<section class="projects">
  <h2 class="heading">Featured Projects</h2>
  <p class="lead">Brief details of new and popular projects. To view full listings, you will be required to sign up and <span class="hl">become a member.</span></p>
  <div class="project-row">
    <article class="project featured">
      <div class="project-photo photo-a" role="img" aria-label="Brick family house with a double garage"><span class="price-tag">From GBP 3,600</span><span class="launch-tag">New Launch</span></div>
      <div class="project-body"><h3>14 Harbour Row LONDON E1</h3><p>Lorem Ipsum is simply dummy text of the printing and typesetting industry. Lorem Ipsum has been the industry's...</p></div>
      <div class="project-funding"><div class="funded">Funded</div><div class="bar"><div class="bar-fill" style="width:50%"></div><span>50%</span></div><div class="details">See Project Details</div></div>
    </article>
    <article class="project">
      <div class="project-photo photo-b" role="img" aria-label="Suburban house with gabled roof and garage"><span class="price-tag">From GBP 3,600</span><span class="launch-tag">New Launch</span></div>
      <div class="project-body"><h3>14 Harbour Row LONDON E1</h3><p>Lorem Ipsum is simply dummy text of the printing and typesetting industry. Lorem Ipsum has been the industry's...</p></div>
      <div class="project-funding"><div class="funded">Funded</div><div class="bar"><div class="bar-fill" style="width:75%"></div><span>75%</span></div><div class="details">See Project Details</div></div>
    </article>
    <article class="project">
      <div class="project-photo photo-c" role="img" aria-label="White Mediterranean villa among palm trees"><span class="price-tag">From GBP 3,600</span><span class="launch-tag">New Launch</span></div>
      <div class="project-body"><h3>14 Harbour Row LONDON E1</h3><p>Lorem Ipsum is simply dummy text of the printing and typesetting industry. Lorem Ipsum has been the industry's...</p></div>
      <div class="project-funding"><div class="funded">Funded</div><div class="bar"><div class="bar-fill" style="width:40%"></div><span>40%</span></div><div class="details">See Project Details</div></div>
    </article>
  </div>
</section>

<section class="community">
  <div class="community-backdrop" role="img" aria-label="Dark city skyline photograph seen from above"></div>
  <h2 class="heading">Be Part of a Growing International Community</h2>
  <p class="lead">Gain access to new projects in world class cities and join our growing community of international landlords.</p>
  <div class="stats">
    <div class="stat"><div class="stat-map" role="img" aria-label="World map with location pins"></div><div class="stat-figure">3,200 barons<br>in 6 countries</div><div class="stat-label">A community of international<br>property barons.</div></div>
    <div class="stat"><div class="stat-map" role="img" aria-label="Group of people silhouettes"></div><div class="stat-figure">USD$ 16.2 million</div><div class="stat-label">Collective buying power of<br>the pennyduke community</div></div>
    <div class="stat"><div class="stat-map" role="img" aria-label="World map with location pins"></div><div class="stat-figure">64 proposals in 6<br>countries</div><div class="stat-label">Attractive real estate from<br>around the world</div></div>
  </div>
</section>

<section class="press">
  <div class="press-box">
    <div class="press-row first"><span class="badge" style="width:112px"></span><span class="badge" style="width:150px"></span><span class="badge" style="width:112px"></span><span class="badge" style="width:336px"></span></div>
    <div class="press-row second"><span class="badge" style="width:64px"></span><span class="badge" style="width:128px"></span><span class="badge" style="width:40px;height:36px"></span><span class="badge" style="width:70px;height:40px"></span><span class="badge" style="width:140px"></span></div>
  </div>
  <div class="press-tag">Featured In</div>
</section>

<div class="skyline" role="img" aria-label="Grey skyline of world landmark cities"></div>
<div class="footer-bar">Follow us on <span class="social-box"></span><span class="social-box"></span><span class="copy">© pennyduke 2014</span></div>

<footer class="legal">
  <span class="group-name">sprout ledger</span>
  <p class="intro-note"><span class="hl">Penny Duke</span> is part of the Sprout Ledger Group. The Sprout Ledger Group is a worldwide pioneer and leader in the crowd investing, peer to peer and online investment market.</p>
  <p>By accessing this site and any pages thereof, you agree to be bound by the terms and conditions. This website is only suitable, intended and available for professional or sophisticated, or similar investors in other jurisdictions, or those who are members of pennyduke community and familiar with, and willing to, accept the risks associated with private participation. Pennyduke does not endorse any of the projects that appear on this website, nor does it make any recommendations regarding the appropriateness of particular opportunities for any participant. Each potential participant must review and evaluate the projects in his or her own discretion and determine the suitability of participating.</p>
  <p>This website (the "Site") is in every respect unaffiliated with any site to which it links or to any company or entity (and connected projects, investment opportunity or similar) featured on this Site, and is not meant as an endorsement of any of those companies or entities ("third parties"). Furthermore and for the avoidance of doubt, Pennyduke Limited is in no way affiliated with any third parties featured or referenced on this Site. There is no commercial relationship between Pennyduke Limited and such third parties, nor an agency arrangement or similar. If you believe your Content (including third party content) as each such term is defined in our Terms of Service has been reproduced on the Site without permission, please refer to our Terms of Service for information on how to request its removal from the Site.</p>
</footer>

</body>
</html>
```